Corvane Card

The logo is the Spanish flag colors I want a vibrant eye catching design with the yellow / red colors over either Navy or white background or black even ,
Would like a 2D feel to the logo with another lighter color logo under it look ,

Contact Information for Business Card

Corvane Flooring
Teodor Vashkin
Main Number
Cell Number
Fax Number

Website on the side of the card somewhere

Font styles to use
Sans Serif

Colors
ec1f27
ffc214

Requirements
Must have
• 2 logos feel one is bolder and the other one underneath very light

```html
<!DOCTYPE html>
<html lang="en">
<head>
<meta charset="utf-8">
<title>Corvane Flooring – Business Cards</title>
<link rel="stylesheet" href="https://fonts.googleapis.com/css2?family=Jost:wght@500;600&family=Arimo:wght@400&display=swap">
<style>
  :root {
    --red: #ec1f27;
    --yellow: #ffc214;
    --navy: #050125;
    --white: #ffffff;
    --rule: #4a4a66;
    --stage: #b4b4b4;
  }
  * { margin: 0; padding: 0; box-sizing: border-box; }
  html, body { width: 1200px; height: 1200px; overflow: hidden; }
  body { background: var(--stage); position: relative; font-family: "Arimo", Arial, sans-serif; }

  .card {
    position: absolute;
    top: 303px;
    width: 368px;
    height: 593px;
    background: var(--navy);
    text-align: center;
  }
  .card--front { left: 201px; }
  .card--back { left: 600px; }

  .brand-square {
    position: absolute;
    left: 50%;
    width: 80px;
    height: 80px;
    margin-left: -40px;
    background: var(--red);
  }
  .card--front .brand-square { top: 210px; }
  .card--back .brand-square { top: 93px; }

  .wordmark {
    position: absolute;
    left: 0; right: 0;
    font-family: "Jost", "Futura", sans-serif;
    font-weight: 600;
    line-height: 1;
  }
  .wordmark__name { display: block; font-size: 44px; letter-spacing: 2px; color: var(--red); }
  .wordmark__trade { display: block; font-size: 20px; letter-spacing: 19px; margin-top: 8px; padding-left: 19px; color: var(--yellow); }
  .card--front .wordmark { top: 322px; }
  .card--back .wordmark { top: 205px; }

  .holder {
    position: absolute;
    top: 357px; left: 0; right: 0;
    font-family: "Jost", sans-serif;
    font-weight: 500;
    font-size: 25px;
    line-height: 1;
  }
  .holder__first { color: var(--red); }
  .holder__last { color: var(--yellow); }

  .divider {
    position: absolute;
    left: 50%;
    width: 64px;
    margin-left: -32px;
    border-top: 1px solid var(--rule);
  }
  .divider--top { top: 396px; }
  .divider--bottom { top: 493px; }

  .contact {
    position: absolute;
    top: 414px; left: 0; right: 0;
    list-style: none;
    font-size: 17px;
    line-height: 21.5px;
    color: var(--white);
  }
  .contact__label { color: var(--red); }

  .email {
    position: absolute;
    top: 508px; left: 0; right: 0;
    font-size: 17px;
    color: var(--white);
  }

  .web {
    position: absolute;
    left: 0; right: 0;
    font-size: 17px;
    color: var(--red);
  }
  .web__domain { color: var(--yellow); }
  .card--front .web { top: 530px; }
  .card--back .web { top: 529px; }
</style>
</head>
<body>

  <section class="card card--front" aria-label="Card front">
    <div class="brand-square"></div>
    <h1 class="wordmark">
      <span class="wordmark__name">CORVANE</span>
      <span class="wordmark__trade">FLOORING</span>
    </h1>
    <p class="web">www.<span class="web__domain">corvanefloor</span>.com</p>
  </section>

  <section class="card card--back" aria-label="Card back">
    <div class="brand-square"></div>
    <h2 class="wordmark">
      <span class="wordmark__name">CORVANE</span>
      <span class="wordmark__trade">FLOORING</span>
    </h2>
    <p class="holder"><span class="holder__first">TEODOR</span> <span class="holder__last">VASHKIN</span></p>
    <div class="divider divider--top"></div>
    <ul class="contact">
      <li><span class="contact__label">P:</span> 312 640 1875</li>
      <li><span class="contact__label">M:</span> 312 907 2246</li>
      <li><span class="contact__label">F:</span> 312 640 1890</li>
    </ul>
    <div class="divider divider--bottom"></div>
    <p class="email">info@corvanefloor.com</p>
    <p class="web">www.<span class="web__domain">corvanefloor</span>.com</p>
  </section>

</body>
</html>
```